Mindfulness School for Children -- Business Cards

We're looking for business cards for our school directors and owners. We're a mindfulness school for children called little lanterns. Attached are our logos/icons.

```html
<!DOCTYPE html>
<html lang="en">
<head>
<meta charset="utf-8">
<title>little lanterns – Business Cards</title>
<link href="https://fonts.googleapis.com/css2?family=Arimo:wght@400;700&display=swap" rel="stylesheet">
<style>
  :root {
    --backdrop: #d9d8d6;
    --card: #262626;
    --card-deep: #111112;
    --pattern-light: #8d8d8f;
    --teal: #4fb3cc;
    --mint: #8fd3b8;
    --ink: #f1f1f1;
    --rule: #5fb7b0;
  }
  * { box-sizing: border-box; margin: 0; padding: 0; }
  html, body {
    width: 1200px; height: 801px; overflow: hidden;
    background: var(--backdrop);
    font-family: "Arimo", Arial, sans-serif;
  }
  .stage {
    position: relative; width: 1200px; height: 801px;
    display: flex; align-items: center; justify-content: center; gap: 40px;
  }
  .card {
    position: relative; width: 520px; height: 297px;
    background: var(--card);
    border-bottom: 4px solid var(--teal);
    overflow: hidden;
  }
  /* Front */
  .card-front .brand-block {
    position: absolute; left: 0; top: 0; width: 250px; height: 100%;
    display: flex; align-items: center; justify-content: center; gap: 10px;
  }
  .brand-mark {
    width: 14px; height: 14px; border-radius: 50%; background: var(--teal);
  }
  .brand-name {
    font-family: "Arimo", Arial, sans-serif; font-weight: 400;
    font-size: 26px; color: var(--teal); letter-spacing: 0.3px;
  }
  .divider {
    position: absolute; left: 262px; top: 78px; width: 1px; height: 140px;
    background: var(--rule);
  }
  .contact {
    position: absolute; left: 284px; top: 74px; color: var(--ink);
  }
  .contact .person-name {
    font-weight: 700; font-size: 17px; letter-spacing: 0.5px; color: var(--teal);
  }
  .contact .person-role { font-size: 11px; margin: 3px 0 12px; }
  .contact ul { list-style: none; font-size: 10.5px; line-height: 1.65; }
  .contact li { display: flex; align-items: center; gap: 6px; }
  .contact li svg { width: 9px; height: 9px; fill: var(--teal); flex: none; }
  .contact address { font-style: normal; font-size: 10.5px; line-height: 1.55; margin-top: 12px; }
  /* Back */
  .card-back .pattern-field {
    position: absolute; inset: 0;
    background: linear-gradient(215deg, var(--pattern-light) 0%, #4a4a4c 30%, var(--card-deep) 62%, #0c0c0d 100%);
    opacity: 0.85;
  }
  .card-back .brand-block {
    position: absolute; right: 40px; bottom: 70px;
    display: flex; align-items: center; gap: 10px;
  }
  .card-back .brand-name { font-size: 30px; }
</style>
</head>
<body>
<main class="stage">
  <section class="card card-front" aria-label="Business card front">
    <div class="brand-block">
      <span class="brand-mark"></span>
      <span class="brand-name">little lanterns</span>
    </div>
    <div class="divider"></div>
    <div class="contact">
      <p class="person-name">NORA WHITFIELD</p>
      <p class="person-role">CEO/Founder</p>
      <ul>
        <li><svg viewBox="0 0 10 10"><path d="M2 0 4 2.5 3 3.6Q4.2 6 6.4 7L7.5 6 10 8 8.5 10Q1 8.5 0 1.5Z"/></svg>(00) 5820 1934</li>
        <li><svg viewBox="0 0 10 10"><path d="M0 2h10v6H0Z M0 2l5 3.5L10 2" stroke="#262626" stroke-width="0.8"/></svg>info@littlelanterns.com</li>
        <li><svg viewBox="0 0 10 10"><circle cx="5" cy="5" r="5"/></svg>www.littlelanterns.com</li>
      </ul>
      <address>Po Box 4412 Elm Street<br>Country Name, AB 20318</address>
    </div>
  </section>
  <section class="card card-back" aria-label="Business card back">
    <div class="pattern-field" role="img" aria-label="Repeating glossy flower pattern fading from dark to light grey"></div>
    <div class="brand-block">
      <span class="brand-mark"></span>
      <span class="brand-name">little lanterns</span>
    </div>
  </section>
</main>
</body>
</html>
```